RW Framewell Inc Business cards

We need business cards using our existing logo but slightly modified. Right now the logo says RW Loadbearing Masonry. We want to keep the RW part of the design, but replace the Structural Concrete portion with "FRAMEWELL". Please see the attached file.
Ideally this would be a blank template so we can add Different Names, titles, and phone numbers later.
On the one side we want only the logo and on the other side the detail. I'm attaching an example for you to see.
Please reach out with any other questions. Our address and other details will be given out once we find a design we like.

Target Market(s)

Construction Industry

```html
<!DOCTYPE html>
<html lang="en">
<head>
<meta charset="utf-8">
<title>RW Framewell Inc – Business Cards</title>
<link rel="stylesheet" href="https://fonts.googleapis.com/css2?family=Montserrat:wght@800&family=Arimo:wght@400&display=swap">
<style>
  :root {
    --brand-blue: #1f75bf;
    --brand-grey: #808285;
    --ink: #1e1e1e;
    --paper: #ffffff;
    --backdrop: #e9ebee;
  }
  * { box-sizing: border-box; margin: 0; padding: 0; }
  html, body {
    width: 1200px;
    height: 900px;
    overflow: hidden;
    background: var(--backdrop);
  }
  .sheet {
    position: relative;
    width: 1200px;
    height: 900px;
  }
  .card {
    position: absolute;
    left: 250px;
    width: 700px;
    height: 400px;
    overflow: hidden;
    box-shadow: 0 8px 24px rgba(0,0,0,0.18);
  }
  .card--front {
    top: 40px;
    background: var(--brand-blue);
    display: flex;
    align-items: center;
    justify-content: center;
  }
  .card--back {
    top: 470px;
    background: var(--paper);
  }
  .wordmark {
    font-family: "Montserrat", sans-serif;
    font-weight: 800;
    letter-spacing: 0.04em;
    white-space: nowrap;
  }
  .wordmark--front {
    color: var(--paper);
    font-size: 58px;
  }
  .wordmark--back {
    position: absolute;
    top: 78px;
    right: 42px;
    color: var(--brand-blue);
    font-size: 34px;
  }
  .holder {
    position: absolute;
    top: 82px;
    left: 58px;
  }
  .holder__name {
    font-family: "Montserrat", sans-serif;
    font-weight: 800;
    font-size: 24px;
    color: var(--brand-blue);
    letter-spacing: 0.01em;
  }
  .holder__title {
    font-family: "Arimo", sans-serif;
    font-size: 17px;
    color: var(--ink);
    margin-top: 2px;
  }
  .contact {
    position: absolute;
    top: 212px;
    left: 60px;
    list-style: none;
    font-family: "Arimo", sans-serif;
    font-size: 19px;
    color: var(--ink);
  }
  .contact__item {
    display: flex;
    align-items: center;
    gap: 12px;
    margin-bottom: 8px;
  }
  .contact__icon {
    width: 22px;
    height: 22px;
    flex: none;
  }
  .swoosh {
    position: absolute;
    inset: 0;
  }
  .website {
    position: absolute;
    right: 40px;
    bottom: 48px;
    font-family: "Arimo", sans-serif;
    font-size: 17px;
    color: var(--paper);
  }
</style>
</head>
<body>
<main class="sheet">

  <section class="card card--front" aria-label="Card front">
    <p class="wordmark wordmark--front">RW FRAMEWELL</p>
  </section>

  <section class="card card--back" aria-label="Card back">
    <svg class="swoosh" viewBox="0 0 700 400" width="700" height="400" aria-hidden="true">
      <path fill="var(--brand-grey)" d="M0,316 C190,314 360,296 482,226 C370,300 190,332 0,338 Z"/>
      <path fill="var(--brand-blue)" d="M0,346 C200,336 380,310 500,236 C580,186 640,162 700,150 L700,400 L0,400 Z"/>
    </svg>

    <p class="wordmark wordmark--back">RW FRAMEWELL</p>

    <div class="holder">
      <p class="holder__name">DANIEL HARTLEY</p>
      <p class="holder__title">Managing Director</p>
    </div>

    <ul class="contact">
      <li class="contact__item">
        <svg class="contact__icon" viewBox="0 0 24 24" aria-hidden="true">
          <path fill="var(--brand-blue)" d="M6.6 10.8a15.1 15.1 0 0 0 6.6 6.6l2.2-2.2a1 1 0 0 1 1-.25 11.4 11.4 0 0 0 3.6.57 1 1 0 0 1 1 1V20a1 1 0 0 1-1 1A17 17 0 0 1 3 4a1 1 0 0 1 1-1h3.5a1 1 0 0 1 1 1c0 1.25.2 2.45.57 3.57a1 1 0 0 1-.25 1z"/>
        </svg>
        <span>044-987 650 312</span>
      </li>
      <li class="contact__item">
        <svg class="contact__icon" viewBox="0 0 24 24" aria-hidden="true">
          <rect x="2" y="5" width="20" height="14" fill="var(--brand-blue)"/>
          <path d="M2 5 L12 13 L22 5" fill="none" stroke="var(--paper)" stroke-width="1.6"/>
        </svg>
        <span>hello@rwframewell.com</span>
      </li>
    </ul>

    <p class="website">www.rwframewell.com</p>
  </section>

</main>
</body>
</html>
```